larkforge website

commerce website to sell cookeries, brackets, mailboxes and to show off homes built. Modern Steel in design see marlo cycles web page to be like: https://www.marlocycles-demo.com/en/ sorry its bright nest hosting word press divi

must be able to add products to page

Target Market(s)

mainly western states of U.S.

Industry/Entity Type

Building Product

Coding

Coded - Design and coding required

Number of Pages Required

3 page

Font styles to use
Sans Serif

Colors

Designer to choose colors to be used in the design.

Requirements
Must have
• customers to be able to order products from page
• bright nest hosting word press divi

```html
<!DOCTYPE html>
<html lang="en">
<head>
<meta charset="utf-8">
<title>Lark Forge</title>
<link href="https://fonts.googleapis.com/css2?family=Poppins:wght@400;500;600&family=Roboto+Condensed:ital,wght@1,400&display=swap" rel="stylesheet">
<style>
:root{
  --brand:#4a5f8a;
  --brand-light:#5b6e97;
  --ink:#2b2b2b;
  --muted:#444;
  --white:#fff;
  --black:#0c0c0c;
}
*{margin:0;padding:0;box-sizing:border-box}
html,body{width:720px;height:1200px;overflow:hidden;background:var(--white)}
body{position:relative;font-family:"Poppins",sans-serif;color:var(--ink)}
.abs{position:absolute}

.site-header{position:absolute;left:0;top:0;width:720px;height:84px;background:var(--white)}
.brand{position:absolute;left:84px;top:26px;display:flex;align-items:center;gap:6px}
.brand-mark{width:18px;height:18px;border-radius:50%;background:var(--brand)}
.brand-name{font-size:17px;font-weight:500;color:var(--brand);letter-spacing:.5px}
.top-contact{position:absolute;top:22px;right:86px;display:flex;align-items:center;font-size:8.5px;font-weight:500;color:#222}
.top-contact .item{display:flex;align-items:center;gap:5px}
.top-contact .sep{width:1px;height:10px;background:#ccc;margin:0 12px}
.main-nav{position:absolute;top:55px;left:338px;display:flex;font-size:9px;color:#222}
.main-nav a{text-decoration:none;color:inherit;margin-right:26px;position:relative;padding-bottom:4px}
.main-nav a:last-child{margin-right:0}
.main-nav a.active::after{content:"";position:absolute;left:-2px;right:-2px;bottom:0;height:1px;background:var(--brand)}

.hero{position:absolute;left:0;top:84px;width:720px;height:354px}
.hero-title{position:absolute;left:0;top:268px;width:720px;text-align:center;color:var(--white);font-size:21px;font-weight:500;line-height:28px;text-shadow:0 1px 3px rgba(0,0,0,.5)}

.section-title{position:absolute;left:0;width:720px;text-align:center;color:var(--brand);font-size:24px;font-weight:400}
.title-rule{position:absolute;height:2px;background:var(--brand)}
.intro{position:absolute;left:92px;top:510px;width:536px;text-align:center;font-size:10px;line-height:17px;color:#333}

.product-card{position:absolute;top:554px;height:211px;background:var(--white);box-shadow:0 3px 6px rgba(0,0,0,.15);text-align:center}
.product-photo{width:100%;height:139px;display:block}
.product-name{margin-top:6px;font-size:13.5px;font-weight:500;color:#333}
.product-rule{width:30px;height:1.5px;background:var(--brand);margin:4px auto 8px}
.product-text{font-size:8px;line-height:14px;color:#333;padding:0 6px}

.shop-button{position:absolute;left:309px;top:787px;width:101px;height:24px;border-radius:12px;background:var(--brand);color:var(--white);display:flex;align-items:center;justify-content:center;gap:5px;font-size:10px;font-weight:600;text-decoration:none}
.shop-button .dot{width:9px;height:9px;border-radius:50%;border:1.5px solid var(--white)}

.goal-rule{position:absolute;height:1.5px;background:var(--brand)}
.goal-text{position:absolute;left:100px;top:918px;width:520px;text-align:center;font-family:"Roboto Condensed",sans-serif;font-style:italic;font-size:23px;line-height:29px;color:#2f2f2f;text-transform:uppercase}

.footer-nav{position:absolute;left:0;top:1066px;width:720px;height:28px;background:var(--brand-light)}
.footer-nav a{position:absolute;top:8px;font-size:9px;color:var(--white);text-decoration:none}
.footer-main{position:absolute;left:0;top:1094px;width:720px;height:80px;background:var(--brand)}
.footer-brand{position:absolute;left:106px;top:31px;display:flex;align-items:center;gap:5px}
.footer-brand .brand-name{color:var(--white);font-size:14px}
.footer-brand .brand-mark{background:var(--white);width:13px;height:13px}
.footer-divider{position:absolute;top:26px;width:1px;height:34px;background:rgba(255,255,255,.3)}
.footer-contact{position:absolute;top:30px;display:flex;gap:6px;color:var(--white);font-size:8.5px;line-height:13px}
.social{position:absolute;top:35px;width:17px;height:17px;border-radius:50%;border:1px solid var(--white)}
.copyright{position:absolute;left:0;top:1174px;width:720px;height:26px;background:var(--black);color:var(--white);font-size:7px;text-align:center;line-height:26px}
</style>
</head>
<body>

<header class="site-header">
  <div class="brand"><span class="brand-mark"></span><span class="brand-name">LARK FORGE</span></div>
  <div class="top-contact">
    <span class="item">
      <svg width="12" height="12" viewBox="0 0 24 24" fill="none" stroke="#4a5f8a" stroke-width="1.8"><path d="M5 3h4l2 5-3 2a12 12 0 0 0 6 6l2-3 5 2v4a2 2 0 0 1-2 2A17 17 0 0 1 3 5a2 2 0 0 1 2-2z"/><path d="M15 3a6 6 0 0 1 6 6M15 7a2 2 0 0 1 2 2"/></svg>
      123.456.7890
    </span>
    <span class="sep"></span>
    <span class="item">
      <svg width="12" height="12" viewBox="0 0 24 24" fill="none" stroke="#4a5f8a" stroke-width="1.8"><rect x="3" y="9" width="18" height="12"/><path d="M3 9l9 7 9-7M6 11V3h12v8"/></svg>
      inquiry@larkforge.com
    </span>
  </div>
  <nav class="main-nav">
    <a class="active" href="#">Home</a>
    <a href="#">Products</a>
    <a href="#">Home Built</a>
    <a href="#">About Us</a>
    <a href="#">Contact Us</a>
  </nav>
</header>

<section class="hero">
  <svg width="720" height="354" viewBox="0 0 720 354" class="abs" style="left:0;top:0">
    <defs>
      <linearGradient id="heroPhoto" x1="0" y1="0" x2="0" y2="1">
        <stop offset="0" stop-color="#9fb6cf"/>
        <stop offset=".45" stop-color="#5d6a6f"/>
        <stop offset=".8" stop-color="#6f6658"/>
        <stop offset="1" stop-color="#8b6f4d"/>
      </linearGradient>
    </defs>
    <polygon points="0,353 370,353 720,353 720,304 370,353 0,303" fill="#fff"/>
    <polygon points="0,303 370,353 720,304 720,310 370,353 0,309" fill="var(--brand)"/>
    <polygon points="0,0 720,0 720,304 370,345 0,303" fill="url(#heroPhoto)" role="img" aria-label="Photo of a modern steel-clad house with large glass windows, trees and palms"/>
    <polygon points="0,303 370,345 720,304 720,310 370,353 0,310" fill="var(--brand)"/>
  </svg>
  <h1 class="hero-title">We Sell Cookeries, Brackets, Mailboxes And To Show<br>Off Homes Built</h1>
</section>

<h2 class="section-title" style="top:466px">Our Products</h2>
<div class="title-rule" style="left:346px;top:500px;width:29px"></div>
<p class="intro">Lorem ipsum dolor sit amet, consectetuer adipiscing elit, sed diam nonummy nibh euismod tincidunt ut laoreet dolore magna aliquam erat volutpat Ut wisi enim ad minim.</p>

<article class="product-card" style="left:84px;width:175px">
  <svg class="product-photo" role="img" aria-label="Photo of a steel-panelled entrance with glass doors"><rect width="100%" height="100%" fill="#5a5d5e"/></svg>
  <h3 class="product-name">Steel Cookery</h3>
  <div class="product-rule"></div>
  <p class="product-text">Lorem ipsum dolor sit amet, consectetuer adipiscing elit, sed diam</p>
</article>
<article class="product-card" style="left:272px;width:177px">
  <svg class="product-photo" role="img" aria-label="Photo of a modern house with steel brackets"><rect width="100%" height="100%" fill="#7d8a92"/></svg>
  <h3 class="product-name">Brackets</h3>
  <div class="product-rule"></div>
  <p class="product-text">Lorem ipsum dolor sit amet, consectetuer adipiscing elit, sed diam</p>
</article>
<article class="product-card" style="left:460px;width:175px">
  <svg class="product-photo" role="img" aria-label="Photo of a round steel fire pit cooker in a workshop"><rect width="100%" height="100%" fill="#8e8c88"/></svg>
  <h3 class="product-name">Mail Boxes</h3>
  <div class="product-rule"></div>
  <p class="product-text">Lorem ipsum dolor sit amet, consectetuer adipiscing elit, sed diam</p>
</article>

<a class="shop-button" href="#"><span class="dot"></span>SHOP NOW</a>

<div class="goal-rule" style="left:130px;top:889px;width:206px"></div>
<div class="goal-rule" style="left:384px;top:889px;width:206px"></div>
<svg class="abs" style="left:342px;top:876px" width="36" height="28" viewBox="0 0 36 28">
  <circle cx="22" cy="14" r="11" fill="none" stroke="#4a5f8a" stroke-width="2"/>
  <circle cx="22" cy="14" r="6.5" fill="none" stroke="#4a5f8a" stroke-width="2"/>
  <circle cx="22" cy="14" r="2.5" fill="#4a5f8a"/>
  <path d="M22 14L4 6" stroke="#4a5f8a" stroke-width="1.8"/>
  <path d="M2 3l6 1-2 5z" fill="#4a5f8a"/>
</svg>
<p class="goal-text">Our goal is simply to build the best products in the world</p>
<div class="goal-rule" style="left:130px;top:987px;width:460px"></div>

<nav class="footer-nav">
  <a href="#" style="left:202px">Home</a>
  <a href="#" style="left:252px">Products</a>
  <a href="#" style="left:315px">Home Built</a>
  <a href="#" style="left:387px">About Us</a>
  <a href="#" style="left:450px">Contact Us</a>
</nav>

<footer class="footer-main">
  <div class="footer-brand"><span class="brand-mark"></span><span class="brand-name">LARK FORGE</span></div>
  <div class="footer-divider" style="left:216px"></div>
  <div class="footer-contact" style="left:244px">
    <svg width="12" height="12" viewBox="0 0 24 24" fill="none" stroke="#fff" stroke-width="1.8"><rect x="3" y="9" width="18" height="12"/><path d="M3 9l9 7 9-7M6 11V3h12v8"/></svg>
    <div>Email Us<br>inquiry@larkforge.com</div>
  </div>
  <div class="footer-divider" style="left:389px"></div>
  <div class="footer-contact" style="left:417px">
    <svg width="13" height="13" viewBox="0 0 24 24" fill="none" stroke="#fff" stroke-width="1.8"><path d="M5 3h4l2 5-3 2a12 12 0 0 0 6 6l2-3 5 2v4a2 2 0 0 1-2 2A17 17 0 0 1 3 5a2 2 0 0 1 2-2z"/><path d="M15 3a6 6 0 0 1 6 6M15 7a2 2 0 0 1 2 2"/></svg>
    <div>Call Us On<br>123.456.7890</div>
  </div>
  <div class="footer-divider" style="left:529px"></div>
  <span class="social" style="left:557px" aria-label="Social link"></span>
  <span class="social" style="left:577px" aria-label="Social link"></span>
  <span class="social" style="left:598px" aria-label="Social link"></span>
</footer>

<div class="copyright">Copyright © 2020 Lark Forge. All Rights Reserved.</div>

</body>
</html>
```